Wine Shop Banners

Banner graphic/images required
Require banner images to match the present online wine shop.

www.talvenhof-wein.de

The wine-shop presently has a very clean, simple design, lots of white space, which is very much the trend at the moment.

Requirements
Images or graphic design for present banners visible on the homepage

The colour and feeling of the banners must fit in with the present clean, simple design.

Work required
3 large slide-card/banners (can be more) and 3 smaller fixed banners below. Please view website to see present position of banners.

LARGE BANNERS x 3

Something special with white background within the banner space
White background on each slide-card. Small individual graphic image in the middle of the slide card. This could be either a simple element of wine:
ingredients, fruit (grape), bottle, cork, old bottle label etc. just displaying one item on each slide-card. Preferably with high quality graphic features.

Note:
We are trying the steer away from the classic stereotype wineshop design. The image/s should have a higher, individual graphic touch, which gives the design something different. Sometimes such artistic work is displayed in steampunk or even in nostalgic design, which leaves the viewer slightly memorized with the content.
To clarify: we are not looking for a full steampunk design but possibly certain elements of this will give you an idea what we mean. That is to say, the design can go slightly in this direction without going over the top. Something small but very eye-catching.

SMALLER BANNERS x 3

One idea is:
Showing a symbol e.g. - discount sign "%" against a white background but again with a high graphic quality.

Target Market(s)

People interested in purchasing wine.
Ages approx. 25 to 65

Industry/Entity Type

Shop

Requirements
Must have
• Something special with white background
• Small individual graphic image in the middle of the slide card.
Nice to have
• The image/s should have a higher, individual graphic touch, which gives the design something different. Something that leaves the viewer slightly memorized with the content.
Should not have
• Not the typical classical design that is often seen on wine shops.

```html
<!DOCTYPE html>
<html lang="de">
<head>
<meta charset="utf-8">
<title>Talvenhof – Weinshop</title>
<link href="https://fonts.googleapis.com/css2?family=Open+Sans:wght@400;600&family=Cinzel:wght@400&family=Cormorant+Garamond:ital,wght@0,500;1,500&display=swap" rel="stylesheet">
<style>
:root{
  --burgundy:#9b1b45;
  --lime:#c2d24e;
  --filter-head:#b4c25a;
  --price:#a3b62a;
  --text:#555;
  --muted:#8a8a8a;
  --line:#e2e2e2;
  --panel:#f4f3f1;
  --white:#fff;
}
*{box-sizing:border-box;margin:0;padding:0}
html,body{width:1200px;height:799px;overflow:hidden;background:var(--white)}
body{font-family:"Open Sans",sans-serif;color:var(--text);position:relative}
.shop{position:absolute;left:240px;top:0;width:720px;height:799px}
.brand{position:absolute;left:0;top:50px;font-weight:600;font-size:26px;color:var(--burgundy);letter-spacing:.5px}
.search{position:absolute;left:370px;top:26px;display:flex;height:24px}
.search-field{width:180px;border:1px solid var(--line);border-right:none;font-size:10px;color:var(--muted);display:flex;align-items:center;padding-left:6px;gap:6px}
.search-btn{width:28px;background:var(--burgundy);color:var(--white);font-size:9px;font-weight:600;display:flex;align-items:center;justify-content:center}
.account{position:absolute;right:0;top:30px;display:flex;gap:14px;font-size:10px;color:var(--muted);align-items:center}
.account span{display:flex;align-items:center;gap:3px}
.nav{position:absolute;left:0;top:104px;width:720px;display:flex;justify-content:space-between;font-size:12px;color:#666;padding-right:110px}
.sidebar{position:absolute;left:0;top:138px;width:135px;font-size:9.5px}
.detail-bar{background:var(--lime);color:#4d5a12;font-weight:600;font-size:10px;padding:5px 6px;text-transform:uppercase}
.filter h3{color:var(--filter-head);font-weight:400;font-size:11px;text-transform:uppercase;margin:12px 0 5px}
.filter ul{list-style:none;position:relative}
.filter li{line-height:15.5px;color:#555}
.filter li::before{content:"› ";color:#888}
.filter li em{font-style:normal;color:var(--muted)}
.scroll{height:120px;overflow:hidden;border-right:6px solid #eee;position:relative}
.scroll::after{content:"";position:absolute;right:-6px;top:14px;width:6px;height:50px;background:#cfcfcf}
.range{position:relative;height:24px}
.range .track{position:absolute;left:4px;right:4px;top:8px;height:3px;background:#ddd;border-radius:2px}
.range .knob{position:absolute;top:4px;width:10px;height:10px;border:1px solid #aaa;border-radius:50%;background:var(--white)}
.range .label{position:absolute;top:16px;width:100%;text-align:center;color:#666}
.region-search{border:1px solid var(--line);height:24px;font-size:9px;color:var(--muted);padding:5px 6px;margin-bottom:8px}
.main{position:absolute;left:148px;top:138px;width:572px}
.hero{position:relative;height:250px;border:1px solid var(--line);overflow:hidden}
.hero-art{position:absolute;inset:0;background:linear-gradient(90deg,#fbfbfa 0%,#f1f0ee 55%,#ebeae7 100%)}
.hero-bottle{position:absolute;right:0;top:0;width:150px;height:250px;background:linear-gradient(90deg,#2a2a2a,#0e0e0e 60%,#3a3a3a)}
.hero-text{position:absolute;left:28px;top:72px}
.hero-kicker{font-family:"Cinzel",serif;font-size:11px;color:var(--burgundy)}
.hero-title{font-family:"Cinzel",serif;font-size:34px;line-height:42px;color:#2e2e2e;margin-top:4px}
.hero-sub{font-family:"Cormorant Garamond",serif;font-style:italic;font-size:11px;color:#555;margin-top:8px}
.promos{display:flex;gap:8px;margin-top:10px}
.promo{flex:1;height:96px;border:1px solid var(--line);background:var(--panel);text-align:center;display:flex;flex-direction:column;justify-content:center;align-items:center}
.promo-title{font-family:"Cinzel",serif;font-size:19px;color:#444}
.promo-note{font-family:"Cinzel",serif;font-size:7px;color:#777;margin-top:2px}
.promo-figure{font-family:"Cormorant Garamond",serif;font-weight:500;font-size:26px;color:var(--burgundy);line-height:28px}
.promo-off{font-family:"Cinzel",serif;font-size:12px;color:var(--burgundy);line-height:12px}
.featured-head{display:flex;justify-content:space-between;align-items:center;margin-top:14px;padding-bottom:5px;border-bottom:1px solid var(--line)}
.featured-head h2{font-family:"Cormorant Garamond",serif;font-weight:500;font-size:14px;color:#333;display:flex;align-items:center;gap:6px}
.dot{width:10px;height:10px;border:1px solid var(--burgundy);border-radius:50%}
.pager{display:flex;gap:3px}
.pager span{width:14px;height:14px;border:1px solid #bbb;font-size:10px;line-height:12px;text-align:center;color:#777}
.products{display:flex;gap:4px;margin-top:4px}
.card{flex:1;border:1px solid var(--line);height:220px;text-align:center;padding:10px 8px}
.card-img{height:118px;width:46px;margin:0 auto;border-radius:10px 10px 4px 4px}
.img-rose{background:linear-gradient(#c9a3a8,#e8b9c0)}
.img-white{background:linear-gradient(#cfd2c0,#e9eadf)}
.img-red{background:linear-gradient(#3a2025,#1e1114)}
.img-marsala{background:linear-gradient(#c9a16a,#e2cfae)}
.card-name{font-size:9.5px;line-height:12px;color:#555;margin-top:14px;height:26px}
.card-price{color:var(--price);font-size:16px;margin-top:12px}
.card-unit{font-size:8.5px;color:#777;margin-top:4px}
</style>
</head>
<body>
<div class="shop">
  <div class="brand">Talvenhof</div>

  <div class="search">
    <div class="search-field">
      <svg width="10" height="10" viewBox="0 0 10 10"><circle cx="4" cy="4" r="3" fill="none" stroke="#9b1b45" stroke-width="1.3"/><line x1="6.3" y1="6.3" x2="9" y2="9" stroke="#9b1b45" stroke-width="1.3"/></svg>
      Suche
    </div>
    <div class="search-btn">GO</div>
  </div>

  <div class="account">
    <svg width="13" height="14" viewBox="0 0 13 14"><circle cx="6.5" cy="4" r="3" fill="none" stroke="#666"/><path d="M1 13c0-3 2.5-5 5.5-5s5.5 2 5.5 5z" fill="none" stroke="#666"/></svg>
    <span><svg width="15" height="13" viewBox="0 0 15 13"><path d="M1 1h2l2 8h7l2-6H4" fill="none" stroke="#666"/><circle cx="6" cy="11.5" r="1" fill="#666"/><circle cx="11" cy="11.5" r="1" fill="#666"/></svg>(0)</span>
    <span><svg width="14" height="12" viewBox="0 0 14 12"><path d="M7 11L1.5 5.5A3 3 0 0 1 7 2a3 3 0 0 1 5.5 3.5z" fill="none" stroke="#666"/></svg>(0)</span>
  </div>

  <nav class="nav">
    <span>Rotwein</span><span>Weißwein</span><span>Rosewein</span><span>Sekt / Champagner</span><span>Sonderangebote</span><span>Probierpakete</span>
  </nav>

  <aside class="sidebar">
    <div class="detail-bar">Detailsuche</div>
    <div class="filter">
      <h3>Land</h3>
      <ul class="scroll">
        <li>Italien <em>(89)</em></li><li>Frankreich <em>(74)</em></li><li>Deutschland <em>(61)</em></li><li>Spanien <em>(35)</em></li><li>Südafrika <em>(15)</em></li><li>Australien <em>(12)</em></li><li>Österreich <em>(11)</em></li><li>Portugal <em>(10)</em></li>
      </ul>
    </div>
    <div class="filter">
      <h3>Geschmack</h3>
      <ul><li>Trocken <em>(307)</em></li><li>Halbtrocken <em>(9)</em></li><li>Lieblich <em>(5)</em></li><li>Süß <em>(2)</em></li><li>Edelsüss <em>(1)</em></li></ul>
    </div>
    <div class="filter">
      <h3>Farbe</h3>
      <ul><li>Rot <em>(157)</em></li><li>Weiß <em>(129)</em></li><li>Prickelnd <em>(22)</em></li><li>Rosé <em>(13)</em></li><li>Champagner <em>(9)</em></li></ul>
    </div>
    <div class="filter">
      <h3>Preis</h3>
      <div class="range"><div class="track"></div><div class="knob" style="left:0"></div><div class="knob" style="right:0"></div><div class="label">2 € - 75 €</div></div>
    </div>
    <div class="filter">
      <h3>Region</h3>
      <div class="region-search">Region suchen ...</div>
      <ul class="scroll" style="height:70px">
        <li>Abruzzen <em>(4)</em></li><li>Alentejo <em>(2)</em></li><li>Apulien <em>(10)</em></li><li>Baden <em>(6)</em></li>
      </ul>
    </div>
  </aside>

  <main class="main">
    <section class="hero">
      <div class="hero-art" role="img" aria-label="Engraved-style illustration of a vineyard landscape with a village on the horizon"></div>
      <div class="hero-bottle" role="img" aria-label="Dark wine bottle against a black panel"></div>
      <div class="hero-text">
        <div class="hero-kicker">Lorem ipsum dolor sit amet, consectetur</div>
        <div class="hero-title">Royal Quality<br>Wine</div>
        <div class="hero-sub">Surprise of Wine Gifts for Someone Special</div>
      </div>
    </section>

    <section class="promos">
      <div class="promo">
        <div class="promo-title">Free Shipping</div>
        <div class="promo-note">On orders over</div>
        <div class="promo-figure">$25</div>
      </div>
      <div class="promo">
        <div class="promo-title">Celebrate</div>
        <div class="promo-note">Your anniversary with taste</div>
      </div>
      <div class="promo">
        <div class="promo-title">Special Offer</div>
        <div class="promo-figure">20%</div>
        <div class="promo-off">Off</div>
      </div>
    </section>

    <section>
      <div class="featured-head">
        <h2><span class="dot"></span>Ausgewählte Produkte</h2>
        <div class="pager"><span>‹</span><span>›</span></div>
      </div>
      <div class="products">
        <div class="card">
          <div class="card-img img-rose" role="img" aria-label="Bottle of rosé sparkling wine"></div>
          <div class="card-name">Pinot Rosé, Villa Serena, Spumante Brut</div>
          <div class="card-price">9,80 €*</div>
          <div class="card-unit">13,07 € per Liter</div>
        </div>
        <div class="card">
          <div class="card-img img-white" role="img" aria-label="Bottle of white wine"></div>
          <div class="card-name">Lugana San Vito della Riva, Casalverde</div>
          <div class="card-price">11,95 €*</div>
          <div class="card-unit">15,93 € per Liter</div>
        </div>
        <div class="card">
          <div class="card-img img-red" role="img" aria-label="Bottle of red wine"></div>
          <div class="card-name">Brouilly, AP, Domaine des Ormeaux</div>
          <div class="card-price">11,95 €*</div>
          <div class="card-unit">15,93 € per Liter</div>
        </div>
        <div class="card">
          <div class="card-img img-marsala" role="img" aria-label="Bottle of Marsala dessert wine"></div>
          <div class="card-name">Marsala Superiore Secco, Bellaria</div>
          <div class="card-price">14,80 €*</div>
          <div class="card-unit">19,73 € per Liter</div>
        </div>
      </div>
    </section>
  </main>
</div>
</body>
</html>
```